Jolly Paws Business Card Update

I have a business card which I love. I want to keep the same logo, colours, font and style. I want to upgrade the scripting and remove some elements and add others.
On the front side under Services - remove the existing wording and insert - Providing individual coaching strategies to create happy, healthy and social canine companions
Under Denise Carvell amend the current wording to read: Qualified in Dog Behavioural Training, Natural Animal Healthcare and Animal Health Science
On the reverse side to remove the web address.

```html
<!DOCTYPE html>
<html lang="en">
<head>
<meta charset="utf-8">
<title>Jolly Paws Business Card</title>
<link rel="stylesheet" href="https://fonts.googleapis.com/css2?family=Arimo:wght@400;700&family=Open+Sans:ital,wght@1,400&family=Ubuntu:wght@400;500&display=swap">
<style>
  :root {
    --page: #2b2b2b;
    --blue-deep: #26398a;
    --blue-mid: #1a62ad;
    --blue-light: #0a90d0;
    --red-dark: #6e1a1c;
    --red-bright: #cc1f26;
    --ring: #b51f25;
    --cream: #ede6d2;
    --white: #ffffff;
    --text-soft: #e8eef8;
  }
  * { box-sizing: border-box; margin: 0; padding: 0; }
  html, body {
    width: 1200px; height: 1138px; overflow: hidden;
    background: var(--page);
  }
  .canvas { position: relative; width: 1200px; height: 1138px; }
  .card {
    position: absolute;
    width: 620px; height: 375px;
    border-radius: 14px;
    overflow: hidden;
    background: linear-gradient(30deg, var(--blue-deep) 0%, var(--blue-mid) 50%, var(--blue-light) 100%);
    box-shadow: 0 4px 10px rgba(0,0,0,0.45);
    color: var(--white);
  }
  .card--front { left: 274px; top: 186px; }
  .card--back { left: 276px; top: 608px; }
  .band {
    position: absolute; left: 0; right: 0; bottom: 0; height: 52px;
    background: linear-gradient(90deg, var(--red-dark) 0%, var(--red-bright) 50%, var(--red-dark) 100%);
    display: flex; align-items: center; justify-content: center;
    font-family: "Arimo", Arial, sans-serif; font-size: 16px; color: var(--text-soft);
  }
  .brand-name {
    position: absolute; left: 35px; top: 54px;
    font-family: "Arimo", Arial, sans-serif; font-weight: 400;
    font-size: 38px; line-height: 1; letter-spacing: 1px; color: var(--text-soft);
  }
  .tagline {
    position: absolute; left: 33px; top: 91px;
    font-family: "Open Sans", Arial, sans-serif; font-style: normal;
    font-size: 18px; line-height: 22px; color: var(--text-soft); letter-spacing: 0.2px;
  }
  .services { position: absolute; left: 38px; top: 177px; width: 240px;
    font-family: "Arimo", Arial, sans-serif; color: var(--text-soft); }
  .services h2 { font-size: 16.5px; font-weight: 700; line-height: 20px; }
  .services p { font-size: 16px; line-height: 19px; }
  .badge {
    position: absolute; border-radius: 50%;
    background: var(--cream);
    border: 20px solid var(--ring);
    box-shadow: 0 0 0 2px var(--cream);
    display: flex; align-items: center; justify-content: center;
    font-family: "Arimo", Arial, sans-serif; color: var(--blue-mid);
    text-align: center;
  }
  .badge--front { left: 330px; top: 40px; width: 256px; height: 256px; font-size: 30px; }
  .badge--back { left: 64px; top: 85px; width: 166px; height: 166px; border-width: 13px; font-size: 20px; }
  .person { position: absolute; left: 292px; top: 76px; }
  .person-name { font-family: "Ubuntu", Arial, sans-serif; font-weight: 500; font-size: 28px; line-height: 32px; color: var(--white); }
  .credentials { margin-top: 3px; font-family: "Open Sans", Arial, sans-serif; font-style: italic;
    font-size: 15px; line-height: 21px; color: var(--text-soft); }
  .contacts { list-style: none; margin-top: 14px;
    font-family: "Ubuntu", Arial, sans-serif; font-size: 16.5px; color: var(--text-soft); }
  .contacts li { display: flex; align-items: center; height: 23px; }
  .contacts svg { width: 14px; height: 14px; margin-right: 15px; fill: var(--text-soft); }
</style>
</head>
<body>
<main class="canvas">
  <section class="card card--front">
    <h1 class="brand-name">JOLLY PAWS</h1>
    <p class="tagline">HAPPY DOGS, HAPPY OWNERS</p>
    <div class="services">
      <h2>SERVICES</h2>
      <p>Providing individual coaching strategies to create happy, healthy and social canine companions</p>
    </div>
    <div class="badge badge--front">Jolly Paws</div>
    <div class="band">Promoting communication and connection between dogs and their families</div>
  </section>

  <section class="card card--back">
    <div class="badge badge--back">Jolly Paws</div>
    <div class="person">
      <h2 class="person-name">Denise Carvell</h2>
      <p class="credentials">Qualified in Dog Behavioural Training,<br>Natural Animal Healthcare and<br>Animal Health Science</p>
      <ul class="contacts">
        <li><svg viewBox="0 0 14 14" aria-hidden="true"><path d="M3 0h8v14H3z M4.5 1.5v9h5v-9z M6 11.5h2v1.5H6z" fill-rule="evenodd"/></svg>0412 736 205</li>
        <li><svg viewBox="0 0 14 14" aria-hidden="true"><path d="M0 3h14v9H0z"/><path d="M0 3l7 5 7-5" stroke="#1a62ad" stroke-width="1.3" fill="none"/></svg>hello@jollypaws1.com</li>
      </ul>
    </div>
    <div class="band">Promoting communication and connection between dogs and their families</div>
  </section>
</main>
</body>
</html>
```